New Dental Office Needs an Attractive and user friendly Website Designed

I need a website for a new dental office. The Name is Harrowfield Dentistry. I would like a Modern design with a user friendly interface and usability.
I would like a landing page, a page that lists the services we offer: Cosmetic Dentistry, Implants, Dental Hygiene, Emergency Services, Restorations, Dentures
Target Market(s)
Mid to upper class
Industry/Entity Type
Dentistry
Coding
Number of Pages Required
1 page
Requirements
Must have
- Landing page that has a scheduling option, Procedures, operating hours, and contact us info
Nice to have
- Appealing design, Soft comforting colors. Easy to navigate page, Modern and professional.

```html
<!DOCTYPE html>
<html lang="en">
<head>
<meta charset="utf-8">
<title>Harrowfield Dentistry</title>
<link href="https://fonts.googleapis.com/css2?family=DM+Serif+Display&family=Red+Hat+Display:wght@400;500;600;700&family=Lato:wght@400;700&display=swap" rel="stylesheet">
<style>
:root{
  --blue:#1f9ae6;
  --accent:#3f8fe4;
  --ink:#1c1c1c;
  --muted:#6d6d6d;
  --dark:#242222;
  --soft:#f4f4f4;
  --line:#d9d9d9;
  --card-blue:#eaf2fb;
  --white:#ffffff;
  --star:#f4b400;
}
*{margin:0;padding:0;box-sizing:border-box}
html,body{width:1200px;height:3064px;overflow:hidden}
body{position:relative;font-family:"Lato",sans-serif;color:var(--ink);background:var(--white)}
a{color:inherit}

/* header */
.site-header{position:absolute;left:0;top:0;width:1200px;height:96px;background:var(--white)}
.brand{position:absolute;left:141px;top:30px;font-family:"DM Serif Display",serif;font-size:30px;color:#222;white-space:nowrap}
.nav{position:absolute;top:42px;font-family:"Red Hat Display",sans-serif;font-size:14px;font-weight:500;letter-spacing:.3px}
.nav.active{color:var(--blue)}
.btn{position:absolute;display:flex;align-items:center;justify-content:center;gap:8px;background:var(--blue);color:var(--white);border-radius:22px;font-family:"Red Hat Display",sans-serif;font-weight:600;font-size:14px;letter-spacing:.3px;white-space:nowrap}

/* hero */
.hero{position:absolute;left:0;top:96px;width:1200px;height:532px;background:linear-gradient(100deg,#e9f1f6 0%,#f7fafc 45%,#eaf1f6 100%);overflow:hidden}
.hero-photo{position:absolute;left:640px;top:0;width:560px;height:532px;background:radial-gradient(ellipse at 55% 45%,#d9b8a2 0%,#c9a38c 25%,#e6eef3 60%,#eef3f7 100%)}
.hero-props{position:absolute;left:0;top:330px;width:180px;height:202px;background:radial-gradient(ellipse at 60% 55%,#ffffff 0%,#eef2f5 55%,rgba(238,242,245,0) 75%)}
.hero h1{position:absolute;left:141px;top:96px;font-family:"DM Serif Display",serif;font-weight:400;font-size:55px;line-height:64px;color:#1b1b1b;width:500px}
.hero .lead{position:absolute;left:139px;top:295px;font-family:"Red Hat Display",sans-serif;font-size:22px;line-height:32px;color:#1b1b1b;width:470px}
.chat-card{position:absolute;left:825px;top:427px;width:210px;height:46px;background:var(--white);border-radius:23px;box-shadow:0 2px 8px rgba(0,0,0,.08);display:flex;align-items:center;padding-left:18px;gap:8px;font-family:"Red Hat Display",sans-serif;font-size:11px;line-height:13px}
.chat-avatar{width:28px;height:28px;border-radius:50%;background:#c8ccd2}
.chat-close{position:absolute;left:821px;top:421px;width:18px;height:18px;border-radius:50%;background:#111;color:#fff;font-size:11px;display:flex;align-items:center;justify-content:center;font-family:"Red Hat Display",sans-serif;font-weight:700}
.chat-bubble{position:absolute;left:1008px;top:418px;width:62px;height:62px;border-radius:50%;background:#1d4fb0;border:4px solid #3a83e0;display:flex;align-items:center;justify-content:center}

/* sections */
.section-title{position:absolute;left:0;width:1200px;text-align:center;font-family:"Red Hat Display",sans-serif;font-weight:600;font-size:30px;color:var(--ink)}
.section-title span,.hl{color:var(--accent)}
.section-sub{position:absolute;left:0;width:1200px;text-align:center;font-size:13px;line-height:16px;color:var(--muted)}

.services{position:absolute;left:0;top:628px;width:1200px;height:618px;background:var(--soft)}
.service-card{position:absolute;width:292px;height:174px;border:1px solid var(--line);border-radius:14px;background:var(--soft);text-align:center}
.service-card.featured{border:2px solid var(--accent);background:var(--white)}
.service-icon{width:42px;height:42px;border-radius:50%;background:#dde8f6;margin:22px auto 0;display:flex;align-items:center;justify-content:center}
.featured .service-icon{background:var(--accent)}
.service-card h3{font-family:"Red Hat Display",sans-serif;font-weight:600;font-size:21px;margin-top:14px}
.featured h3{color:var(--accent)}
.service-card p{font-size:12.5px;line-height:16px;color:var(--muted);margin:6px 22px 0}
.featured p{color:#222}

.why{position:absolute;left:0;top:1246px;width:1200px;height:401px;background:var(--dark);color:var(--white)}
.why h2{position:absolute;left:141px;top:66px;font-family:"Red Hat Display",sans-serif;font-weight:600;font-size:30px;line-height:37px}
.why .intro{position:absolute;left:141px;top:147px;width:270px;font-size:12.5px;line-height:16px;color:#ddd}
.feature{position:absolute;width:285px}
.feature-head{display:flex;align-items:center;gap:14px;font-family:"Red Hat Display",sans-serif;font-weight:500;font-size:21px;white-space:nowrap}
.feature-icon{width:36px;height:36px;border-radius:50%;background:var(--white);display:flex;align-items:center;justify-content:center;flex:none}
.feature p{font-size:12.5px;line-height:16px;color:#ddd;margin-top:12px}
.feature a{display:inline-block;margin-top:13px;font-size:12.5px;text-decoration:underline}

.map{position:absolute;left:141px;top:1833px;width:642px;height:461px;background:linear-gradient(135deg,#a9cdf2 0%,#cfd9e3 45%,#dcdcd8 70%,#b6d3f1 100%)}
.visit-card{position:absolute;left:758px;top:1903px;width:300px;height:322px;background:var(--dark);border-radius:10px;color:var(--white);padding:30px 28px}
.visit-card h4{display:flex;align-items:center;gap:8px;font-family:"Red Hat Display",sans-serif;font-weight:500;font-size:20px}
.visit-card p{font-size:12.5px;line-height:16px;margin-top:6px}
.visit-card .block{margin-bottom:22px}
.call-btn{display:inline-block;background:var(--white);color:#111;border-radius:16px;padding:8px 22px;font-size:12.5px;margin-top:4px}

.review{position:absolute;top:2486px;width:448px;height:192px;background:var(--card-blue);border-radius:12px;padding:22px 21px}
.review-top{display:flex;justify-content:space-between;align-items:center;font-size:12.5px}
.stars{display:flex;gap:5px}
.review blockquote{font-size:12.5px;line-height:16px;margin-top:18px;color:#222}
.reviewer{display:flex;align-items:center;gap:18px;margin-top:14px}
.reviewer .avatar{width:56px;height:56px;border-radius:50%;background:#c7b7a6}
.reviewer strong{display:block;font-family:"Red Hat Display",sans-serif;font-weight:500;font-size:20px}
.reviewer span{font-size:12px;color:var(--muted)}
.arrow{position:absolute;top:2572px;width:29px;height:29px;border-radius:5px;display:flex;align-items:center;justify-content:center}

.site-footer{position:absolute;left:0;top:2823px;width:1200px;height:241px;background:var(--dark);color:var(--white)}
.footer-brand{position:absolute;left:0;width:1200px;top:50px;text-align:center;font-family:"DM Serif Display",serif;font-size:26px}
.footer-nav{position:absolute;left:0;width:1200px;top:126px;display:flex;justify-content:center;gap:28px;font-family:"Red Hat Display",sans-serif;font-size:13px}
.footer-rule{position:absolute;left:0;top:200px;width:1200px;height:1px;background:#444}
.copyright{position:absolute;left:0;width:1200px;top:217px;text-align:center;font-size:11px;color:#ccc}
</style>
</head>
<body>

<header class="site-header">
  <div class="brand">Harrowfield Dentistry</div>
  <span class="nav active" style="left:510px">HOME</span>
  <span class="nav" style="left:593px">SERVICES</span>
  <span class="nav" style="left:700px">CONTACT US</span>
  <div class="btn" style="left:826px;top:30px;width:232px;height:42px">
    <svg width="15" height="15" viewBox="0 0 16 16" fill="none" stroke="#fff" stroke-width="1.4"><rect x="1.5" y="3" width="13" height="11.5" rx="1.5"/><path d="M1.5 6.5h13M5 1.5v3M11 1.5v3"/></svg>
    BOOK AN APPOINTMENT
  </div>
</header>

<section class="hero">
  <div class="hero-photo" role="img" aria-label="Photo of a smiling woman touching her cheek"></div>
  <div class="hero-props" role="img" aria-label="Illustration of a white tooth with a dental mirror"></div>
  <h1>Premium Dental Care for a Confident Smile</h1>
  <p class="lead">Expert Cosmetic And Restorative Dentistry In A Luxurious Setting.</p>
  <div class="btn" style="left:141px;top:385px;width:233px;height:42px">
    <svg width="15" height="15" viewBox="0 0 16 16" fill="none" stroke="#fff" stroke-width="1.4"><rect x="1.5" y="3" width="13" height="11.5" rx="1.5"/><path d="M1.5 6.5h13M5 1.5v3M11 1.5v3"/></svg>
    BOOK AN APPOINTMENT
  </div>
  <div class="chat-card"><div class="chat-avatar"></div><div>Lorem Ipsum Simply<br>Dummy Text.</div></div>
  <div class="chat-close">×</div>
  <div class="chat-bubble">
    <svg width="28" height="26" viewBox="0 0 28 26"><path d="M14 2C7 2 2 6.5 2 12c0 3 1.5 5.6 4 7.4L5 24l5.2-2.7c1.2.3 2.5.5 3.8.5 7 0 12-4.5 12-10S21 2 14 2z" fill="#fff"/><circle cx="9" cy="12" r="1.8" fill="#1d4fb0"/><circle cx="14" cy="12" r="1.8" fill="#1d4fb0"/><circle cx="19" cy="12" r="1.8" fill="#1d4fb0"/></svg>
  </div>
</section>

<section class="services">
  <h2 class="section-title" style="top:48px">Our Dental <span>Services</span></h2>
  <p class="section-sub" style="top:91px">Comprehensive, high-quality care from cosmetic enhancements to<br>emergency treatments—tailored to your smile.</p>

  <div class="service-card" style="left:141px;top:164px">
    <div class="service-icon"><svg width="24" height="24" viewBox="0 0 24 24" fill="none" stroke="#3f8fe4" stroke-width="1.5"><circle cx="12" cy="12" r="9"/><path d="M8 14c1 1.6 2.4 2.4 4 2.4s3-.8 4-2.4"/><circle cx="9" cy="10" r=".8" fill="#3f8fe4"/><circle cx="15" cy="10" r=".8" fill="#3f8fe4"/></svg></div>
    <h3>Cosmetic Dentistry</h3>
    <p>Enhance your smile with treatments that improve tooth shape, color, and appearance.</p>
  </div>
  <div class="service-card featured" style="left:455px;top:164px">
    <div class="service-icon"><svg width="24" height="24" viewBox="0 0 24 24" fill="none" stroke="#fff" stroke-width="1.5"><path d="M7 4c2 0 3 1 5 1s3-1 5-1c2 0 3 2 3 4 0 3-2 4-2 7s-1 6-2 6-1-4-4-4-3 4-4 4-2-3-2-6-2-4-2-7c0-2 1-4 3-4z"/></svg></div>
    <h3>Dental Implants</h3>
    <p>Permanent, natural-looking tooth replacements that restore function and confidence.</p>
  </div>
  <div class="service-card" style="left:768px;top:164px">
    <div class="service-icon"><svg width="24" height="24" viewBox="0 0 24 24" fill="none" stroke="#3f8fe4" stroke-width="1.5"><path d="M5 5l14 14M19 5L5 19"/><circle cx="5" cy="5" r="2"/><circle cx="19" cy="5" r="2"/></svg></div>
    <h3>Emergency Services</h3>
    <p>Quick, professional treatment for dental emergencies, providing relief when you need it most.</p>
  </div>
  <div class="service-card" style="left:141px;top:374px">
    <div class="service-icon"><svg width="24" height="24" viewBox="0 0 24 24" fill="none" stroke="#3f8fe4" stroke-width="1.5"><path d="M3 9c3 2 15 2 18 0M4 10c1 5 4 7 8 7s7-2 8-7"/><path d="M8 11v3M12 11.5v3.5M16 11v3"/></svg></div>
    <h3>Teeth Whitening</h3>
    <p>Brighten your smile with safe, professional whitening treatments that deliver fast, noticeable results.</p>
  </div>
  <div class="service-card" style="left:455px;top:374px">
    <div class="service-icon"><svg width="24" height="24" viewBox="0 0 24 24" fill="none" stroke="#3f8fe4" stroke-width="1.5"><path d="M7 4c2 0 3 1 5 1s3-1 5-1c2 0 3 2 3 4 0 3-2 4-2 7s-1 6-2 6-1-4-4-4-3 4-4 4-2-3-2-6-2-4-2-7c0-2 1-4 3-4z"/><path d="M15 8l1 1.5L17.5 10 16 11l-1 1.5-1-1.5-1.5-1L14 9.5z"/></svg></div>
    <h3>Dental Hygiene</h3>
    <p>Preventive cleanings and exams to keep your teeth and gums healthy, fresh, and cavity-free.</p>
  </div>
  <div class="service-card" style="left:768px;top:374px">
    <div class="service-icon"><svg width="24" height="24" viewBox="0 0 24 24" fill="none" stroke="#3f8fe4" stroke-width="1.5"><path d="M7 4c2 0 3 1 5 1s3-1 5-1c2 0 3 2 3 4 0 3-2 4-2 7s-1 6-2 6-1-4-4-4-3 4-4 4-2-3-2-6-2-4-2-7c0-2 1-4 3-4z"/></svg></div>
    <h3>Tooth Restoration</h3>
    <p>Repair and restore damaged teeth with natural-looking fillings, crowns, and bridges for a healthier smile.</p>
  </div>
</section>

<section class="why">
  <h2>Why Patients<br>Choose <span class="hl">Our Clinic</span></h2>
  <p class="intro">Experience expert care in a modern, comfort-first clinic—where advanced technology meets personalized treatment.</p>

  <div class="feature" style="left:443px;top:70px">
    <div class="feature-head"><span class="feature-icon"><svg width="18" height="18" viewBox="0 0 18 18" fill="none" stroke="#3f8fe4" stroke-width="1.5"><rect x="2" y="4" width="14" height="10" rx="1.5"/><circle cx="9" cy="9" r="2"/></svg></span>Board-Certified Dentists</div>
    <p>Expertise you can trust, backed by advanced training and credentials.</p>
    <a>Learn more</a>
  </div>
  <div class="feature" style="left:765px;top:70px">
    <div class="feature-head"><span class="feature-icon"><svg width="18" height="18" viewBox="0 0 18 18" fill="none" stroke="#3f8fe4" stroke-width="1.5"><path d="M5 3c1.5 0 2.3.8 4 .8S11.5 3 13 3c1.5 0 2 1.5 2 3 0 2.3-1.5 3-1.5 5.3S12.7 16 12 16s-.8-3-3-3-2.3 3-3 3-1.5-2.4-1.5-4.7S3 8.3 3 6c0-1.5.5-3 2-3z"/></svg></span>Pain-Free Treatments</div>
    <p>Gentle techniques and modern technology for a stress-free experience.</p>
    <a>Learn more</a>
  </div>
  <div class="feature" style="left:443px;top:228px">
    <div class="feature-head"><span class="feature-icon"><svg width="18" height="18" viewBox="0 0 18 18" fill="none" stroke="#3f8fe4" stroke-width="1.5"><path d="M3 15l5-5M7 4l7 7M10 2l6 6-3 1-4-4z"/></svg></span>Luxury, Comfort Clinic</div>
    <p>Designed to help you relax—because your comfort matters.</p>
    <a>Learn more</a>
  </div>
  <div class="feature" style="left:765px;top:228px">
    <div class="feature-head"><span class="feature-icon"><svg width="18" height="18" viewBox="0 0 18 18" fill="none" stroke="#3f8fe4" stroke-width="1.5"><rect x="2" y="5" width="14" height="10" rx="1.5"/><path d="M4 5l8-3 1 3M12 10h2"/></svg></span>Flexible Payment Plans</div>
    <p>Quality care made accessible with tailored financing options.</p>
    <a>Learn more</a>
  </div>
</section>

<h2 class="section-title" style="top:1716px">Visit Our <span>Clinic</span></h2>
<p class="section-sub" style="top:1759px">Located in the heart of Harrowfield, our clinic offers<br>flexible hours and easy access to premium dental care.</p>

<div class="map" role="img" aria-label="Street map showing the clinic location"></div>
<div class="visit-card">
  <div class="block">
    <h4><svg width="18" height="18" viewBox="0 0 18 18" fill="none" stroke="#3f8fe4" stroke-width="1.4"><path d="M9 16s5-5 5-9A5 5 0 0 0 4 7c0 4 5 9 5 9z"/><circle cx="9" cy="7" r="1.8"/></svg>Visit Us</h4>
    <p style="padding-left:8px">48 Alder Crescent, Harrowfield</p>
  </div>
  <div class="block">
    <h4><svg width="18" height="18" viewBox="0 0 18 18" fill="none" stroke="#3f8fe4" stroke-width="1.4"><circle cx="9" cy="9" r="7"/><path d="M9 5v4l2.5 2"/></svg>Operating Hours</h4>
    <p>Mon–Fri: 8:00 AM – 6:00 PM<br>Sat: 9:00 AM – 2:00 PM<br>Closed Sundays</p>
  </div>
  <div class="block">
    <h4><svg width="18" height="18" viewBox="0 0 18 18" fill="none" stroke="#3f8fe4" stroke-width="1.4"><path d="M4 2h3l1.5 4-2 1.3a9 9 0 0 0 4.2 4.2L12 9.5l4 1.5v3c0 1-1 2-2 2C8 16 2 10 2 4c0-1 1-2 2-2z"/></svg>Call Us</h4>
    <p>(555) 014-2298</p>
  </div>
  <span class="call-btn">Call Now</span>
</div>

<h2 class="section-title" style="top:2364px">What Our <span>Patients Say</span></h2>
<p class="section-sub" style="top:2407px">Real stories from patients who’ve experienced compassionate care,<br>outstanding results, and a confident new smile.</p>

<div class="arrow" style="left:91px;border:1px solid #333">
  <svg width="12" height="12" viewBox="0 0 12 12" fill="none" stroke="#222" stroke-width="1.6"><path d="M8 1L3 6l5 5"/></svg>
</div>
<div class="review" style="left:141px">
  <div class="review-top">
    <div class="stars">
      <svg width="20" height="19" viewBox="0 0 20 19"><path d="M10 0l3 6.2 6.8.9-5 4.7 1.3 6.7L10 15.3 3.9 18.5l1.3-6.7-5-4.7L7 6.2z" fill="#f4b400"/></svg>
      <svg width="20" height="19" viewBox="0 0 20 19"><path d="M10 0l3 6.2 6.8.9-5 4.7 1.3 6.7L10 15.3 3.9 18.5l1.3-6.7-5-4.7L7 6.2z" fill="#f4b400"/></svg>
      <svg width="20" height="19" viewBox="0 0 20 19"><path d="M10 0l3 6.2 6.8.9-5 4.7 1.3 6.7L10 15.3 3.9 18.5l1.3-6.7-5-4.7L7 6.2z" fill="#f4b400"/></svg>
      <svg width="20" height="19" viewBox="0 0 20 19"><path d="M10 0l3 6.2 6.8.9-5 4.7 1.3 6.7L10 15.3 3.9 18.5l1.3-6.7-5-4.7L7 6.2z" fill="#f4b400"/></svg>
      <svg width="20" height="19" viewBox="0 0 20 19"><path d="M10 0l3 6.2 6.8.9-5 4.7 1.3 6.7L10 15.3 3.9 18.5l1.3-6.7-5-4.7L7 6.2z" fill="#f4b400"/></svg>
    </div>
    <span>10th Feb, 2023</span>
  </div>
  <blockquote>"The team made me feel comfortable from the moment I walked in. My smile has never looked better!"</blockquote>
  <div class="reviewer"><div class="avatar" role="img" aria-label="Portrait photo of the reviewer"></div><div><strong>Owen R.</strong><span>Customer</span></div></div>
</div>
<div class="review" style="left:611px">
  <div class="review-top">
    <div class="stars">
      <svg width="20" height="19" viewBox="0 0 20 19"><path d="M10 0l3 6.2 6.8.9-5 4.7 1.3 6.7L10 15.3 3.9 18.5l1.3-6.7-5-4.7L7 6.2z" fill="#f4b400"/></svg>
      <svg width="20" height="19" viewBox="0 0 20 19"><path d="M10 0l3 6.2 6.8.9-5 4.7 1.3 6.7L10 15.3 3.9 18.5l1.3-6.7-5-4.7L7 6.2z" fill="#f4b400"/></svg>
      <svg width="20" height="19" viewBox="0 0 20 19"><path d="M10 0l3 6.2 6.8.9-5 4.7 1.3 6.7L10 15.3 3.9 18.5l1.3-6.7-5-4.7L7 6.2z" fill="#f4b400"/></svg>
      <svg width="20" height="19" viewBox="0 0 20 19"><path d="M10 0l3 6.2 6.8.9-5 4.7 1.3 6.7L10 15.3 3.9 18.5l1.3-6.7-5-4.7L7 6.2z" fill="#f4b400"/></svg>
      <svg width="20" height="19" viewBox="0 0 20 19"><path d="M10 0l3 6.2 6.8.9-5 4.7 1.3 6.7L10 15.3 3.9 18.5l1.3-6.7-5-4.7L7 6.2z" fill="#f4b400"/></svg>
    </div>
    <span>06th Feb, 2023</span>
  </div>
  <blockquote>"Beautiful clinic, friendly staff, and pain-free treatment. Truly a premium dental experience."</blockquote>
  <div class="reviewer"><div class="avatar" style="background:#d8c08e" role="img" aria-label="Portrait photo of the reviewer"></div><div><strong>Clara V.</strong><span>Customer</span></div></div>
</div>
<div class="arrow" style="left:1080px;background:#111">
  <svg width="12" height="12" viewBox="0 0 12 12" fill="none" stroke="#fff" stroke-width="1.6"><path d="M4 1l5 5-5 5"/></svg>
</div>

<div class="btn" style="left:547px;top:2728px;width:106px;height:40px;font-weight:500;font-size:13px;background:#4a90e2">View All</div>

<footer class="site-footer">
  <div class="footer-brand">Harrowfield Dentistry</div>
  <nav class="footer-nav"><span>Home</span><span>Our Services</span><span>Contact Us</span></nav>
  <div class="footer-rule"></div>
  <p class="copyright">© 2025 Harrowfield Dental Care. All Rights Reserved.</p>
</footer>

</body>
</html>
```